Corvane Card

The logo is the Spanish flag colors I want a vibrant eye catching design with the yellow / red colors over either Navy or white background or black even ,
Would like a 2D feel to the logo with another lighter color logo under it look ,

Contact Information for Business Card

Corvane Flooring
Teodor Vashkin
Main Number
Cell Number
Fax Number

Website on the side of the card somewhere

Font styles to use
Sans Serif

Colors
ec1f27
ffc214

Requirements
Must have
• 2 logos feel one is bolder and the other one underneath very light

```html
<!DOCTYPE html>
<html lang="en">
<head>
<meta charset="utf-8">
<title>Corvane Flooring – Business Card</title>
<link rel="stylesheet" href="https://fonts.googleapis.com/css2?family=Jost:wght@500;600&family=Arimo:wght@400;700&display=swap">
<style>
  :root {
    --brand-red: #ec1f27;
    --brand-yellow: #ffc214;
    --band-red: #dc1d25;
    --band-yellow: #f3b812;
    --paper: #ffffff;
    --ink: #2b2b2b;
    --rule: #b9b9b9;
    --backdrop: #a9a9a9;
  }
  * { margin: 0; padding: 0; box-sizing: border-box; }
  html, body { width: 1200px; height: 1200px; overflow: hidden; }
  body { background: var(--backdrop); position: relative; font-family: "Arimo", Arial, sans-serif; }

  .card { position: absolute; top: 303px; width: 369px; height: 594px; box-shadow: 3px 4px 5px rgba(0,0,0,.45); overflow: hidden; }

  /* Front */
  .card-front { left: 201px; display: flex; }
  .front-half { flex: 1; }
  .front-half--red { background: var(--brand-red); }
  .front-half--yellow { background: var(--brand-yellow); }
  .front-band { position: absolute; left: 0; right: 0; top: 205px; height: 183px; display: flex;
    border-top: 1px solid rgba(0,0,0,.18); border-bottom: 2px solid rgba(0,0,0,.35); }
  .front-band span { flex: 1; }
  .front-band .band-red { background: var(--band-red); }
  .front-band .band-yellow { background: var(--band-yellow); }

  /* Back */
  .card-back { left: 599px; width: 364px; background: var(--paper); text-align: center; }
  .brand-square { position: absolute; left: 151px; top: 96px; width: 62px; height: 62px; background: var(--brand-red); }
  .brand-name { position: absolute; left: 0; right: 0; top: 196px; font-family: "Jost", sans-serif; font-weight: 600;
    color: var(--brand-red); line-height: 1; }
  .brand-name .line-main { display: block; font-size: 37px; letter-spacing: 1px; }
  .brand-name .line-sub { display: block; font-size: 19px; letter-spacing: 17px; margin-top: 12px; margin-right: -17px; }

  .person-name { position: absolute; left: 0; right: 0; top: 356px; font-family: "Jost", sans-serif; font-weight: 600;
    font-size: 25px; letter-spacing: .3px; }
  .person-name .first { color: var(--brand-red); }
  .person-name .last { color: var(--brand-yellow); }

  .rule { position: absolute; left: 150px; width: 64px; height: 1px; background: var(--rule); }
  .rule--top { top: 396px; }
  .rule--bottom { top: 492px; }

  .contact-list { position: absolute; left: 0; right: 0; top: 414px; list-style: none; font-size: 17px; line-height: 21.5px; color: var(--ink); }
  .contact-list b { color: var(--brand-red); }

  .online { position: absolute; left: 0; right: 0; top: 510px; font-size: 16px; line-height: 21.5px; }
  .online .email { color: var(--ink); }
  .online .web { color: var(--brand-red); }
  .online .web em { font-style: normal; color: var(--brand-yellow); }
</style>
</head>
<body>
  <section class="card card-front" aria-label="Card front">
    <div class="front-half front-half--red"></div>
    <div class="front-half front-half--yellow"></div>
    <div class="front-band"><span class="band-red"></span><span class="band-yellow"></span></div>
  </section>

  <section class="card card-back" aria-label="Card back">
    <div class="brand-square"></div>
    <h1 class="brand-name"><span class="line-main">CORVANE</span><span class="line-sub">FLOORING</span></h1>

    <h2 class="person-name"><span class="first">TEODOR</span> <span class="last">VASHKIN</span></h2>
    <div class="rule rule--top"></div>
    <ul class="contact-list">
      <li><b>P:</b> 444 555 2190</li>
      <li><b>M:</b> 888 555 7316</li>
      <li><b>F:</b> 888 444 5082</li>
    </ul>
    <div class="rule rule--bottom"></div>
    <div class="online">
      <div class="email">info@corvaneflooring.com</div>
      <div class="web">www.<em>corvaneflooring</em>.com</div>
    </div>
  </section>
</body>
</html>
```